KDWB Business Card

Looking for a business card design to incorporate our branding. We want to only use the colors listing in the Branding Package (attached).
Updates

Target Market(s)

People who need their phone or device fixed.

Industry/Entity Type

Electronics

Contact Information for Business Card

Please use:

Brightwick Gadget Clinic LLC
4810 E Harlow Ridge Rd
Suite 417
San Antonio, TX 78163

Marcus Delgrove, Store Manager

(210) 555-0147

Requirements
Must have
• Must include the colors that are contained within the Branding Package PDF file.

```html
<!DOCTYPE html>
<html lang="en">
<head>
<meta charset="utf-8">
<title>Brightwick Gadget Clinic — Business Card</title>
<link rel="stylesheet" href="https://fonts.googleapis.com/css2?family=Arimo:wght@400&display=swap">
<style>
  :root {
    --page: #e6e6e6;
    --card: #ffffff;
    --orange: #f0521e;
    --charcoal: #525254;
    --ink: #222222;
    --photo-a: #f4f3f7;
    --photo-b: #e9e9f3;
  }
  * { margin: 0; padding: 0; box-sizing: border-box; }
  html, body { width: 1189px; height: 1200px; overflow: hidden; }
  body {
    background: var(--page);
    font-family: "Arimo", Arial, sans-serif;
    color: var(--ink);
    position: relative;
  }
  .card {
    position: absolute;
    left: 263px;
    width: 663px;
    height: 391px;
    background: var(--card);
    overflow: hidden;
  }
  .card--front { top: 188px; }
  .card--back { top: 620px; }

  .front-photo {
    position: absolute; inset: 0;
    background: linear-gradient(160deg, var(--photo-a) 0%, var(--photo-b) 55%, var(--photo-a) 100%);
  }
  .brand {
    position: absolute;
    display: flex;
    align-items: center;
    color: var(--orange);
    font-weight: 400;
    white-space: nowrap;
  }
  .brand__mark { background: var(--orange); border-radius: 8px; flex: none; }
  .brand--front { left: 130px; top: 164px; font-size: 34px; gap: 18px; }
  .brand--front .brand__mark { width: 62px; height: 62px; border-radius: 12px; }
  .brand--back { left: 100px; top: 76px; font-size: 25px; gap: 13px; }
  .brand--back .brand__mark { width: 46px; height: 46px; }

  .side-band { position: absolute; left: 0; top: 0; bottom: 0; width: 60px; background: var(--charcoal); }
  .side-rule { position: absolute; left: 63px; top: 0; bottom: 0; width: 5px; background: var(--orange); }

  .contact { position: absolute; left: 97px; font-size: 17px; letter-spacing: 0.3px; display: flex; align-items: center; gap: 9px; }
  .contact svg { width: 16px; height: 16px; flex: none; }
  .contact--phone { top: 252px; }
  .contact--email { top: 304px; }
  .contact--web { top: 330px; }

  .person { position: absolute; right: 34px; top: 301px; text-align: right; }
  .person__name { font-size: 23px; letter-spacing: -0.3px; color: var(--ink); }
  .person__title { font-size: 13px; color: var(--orange); margin-top: 5px; }
</style>
</head>
<body>
  <section class="card card--front">
    <div class="front-photo" role="img" aria-label="Faint photo of hands repairing an opened smartphone on a blue work mat"></div>
    <div class="brand brand--front"><span class="brand__mark"></span>Brightwick Gadget Clinic</div>
  </section>

  <section class="card card--back">
    <div class="side-band"></div>
    <div class="side-rule"></div>
    <div class="brand brand--back"><span class="brand__mark"></span>Brightwick Gadget Clinic</div>

    <div class="contact contact--phone">
      <svg viewBox="0 0 16 16" aria-hidden="true"><rect width="16" height="16" fill="#f0521e"/><path d="M5 3.5 L7 3.5 L7.5 6 L6.3 6.8 Q7 9.3 9.2 10.2 L10 9 L12.5 9.5 L12.5 11.8 Q7 12.5 4.5 6 Z" fill="#fff"/></svg>
      (210) 555-0147
    </div>
    <div class="contact contact--email">
      <svg viewBox="0 0 16 16" aria-hidden="true"><rect width="16" height="16" fill="#f0521e"/><rect x="3" y="4.5" width="10" height="7" fill="none" stroke="#fff" stroke-width="1.3"/><path d="M3 4.5 L8 8.5 L13 4.5" fill="none" stroke="#fff" stroke-width="1.3"/></svg>
      marcus@BrightwickGadget.com
    </div>
    <div class="contact contact--web">
      <svg viewBox="0 0 16 16" aria-hidden="true"><rect width="16" height="16" fill="#f0521e"/><circle cx="8" cy="8" r="4.6" fill="none" stroke="#fff" stroke-width="1.3"/><path d="M3.4 8 H12.6 M8 3.4 V12.6" stroke="#fff" stroke-width="1"/></svg>
      www.BrightwickGadget.com
    </div>

    <div class="person">
      <div class="person__name">Marcus Delgrove</div>
      <div class="person__title">Store Manager</div>
    </div>
  </section>
</body>
</html>
```